Bramblecrest Resource Group is a recycling company. We have started a marketing campaign and would love your artwork to help us get started. We would like the fallowing to be on our postcard:
At the top please write: Now servicing businesses in the city of Industry!
Below that we would like 3 pictures.. The first is a picture of trash, the second is a our logo and at plus sign. After that would be a picture of neat baled recycled material and the last picture would be money. Below this please right the following:
- Companies choose bramblecrest resource group because:
- if it can be recycled we will find a use for it
- we pay top dollar
- starting our service is fast and easy
* All it takes is one call/email and we will handle the rest
At the bottom please put our contact information
- 800.514.2976
- delphine@bramble722.com
- bramble722.com

Thanks guys! I have attached our logo!

I am sorry for this late post,but could you not put anything on the back except for a return address which is 4187 Tillery Ave Costa Mesa, Ca 92871 Thank you! We have had a lot of trouble in the past with the post office when we put stuff on the back for some reason.

Recycling

```html
<!DOCTYPE html>
<html lang="en">
<head>
<meta charset="utf-8">
<title>Bramblecrest Resource Group — Postcard</title>
<link rel="stylesheet" href="https://fonts.googleapis.com/css2?family=Abel&family=Cabin+Condensed:wght@400;500&display=swap">
<style>
  :root {
    --green: #79bd43;
    --ink: #5b5a4c;
    --ink-soft: #6d6c62;
    --panel: #d8d8d6;
    --panel-light: #e6e6e4;
    --rule: #8d8c84;
    --paper: #f1f1ee;
    --paper-shade: #dedfda;
    --tag: rgba(214, 214, 210, 0.55);
    --ring: #ffffff;
  }
  * { box-sizing: border-box; margin: 0; padding: 0; }
  html, body { width: 1200px; height: 776px; overflow: hidden; background: #fff; }
  .postcard {
    position: relative; width: 1200px; height: 776px; overflow: hidden;
    font-family: "Cabin Condensed", "Arial Narrow", sans-serif; color: var(--ink);
  }
  .backdrop {
    position: absolute; left: 372px; top: 0; width: 828px; height: 776px;
    background:
      linear-gradient(160deg, rgba(255,255,255,.7) 0%, rgba(255,255,255,0) 40%),
      linear-gradient(200deg, var(--paper) 0%, var(--paper-shade) 55%, var(--paper) 100%);
  }
  .side-panel {
    position: absolute; left: 0; top: 0; width: 372px; height: 776px;
    background: linear-gradient(90deg, var(--panel) 0%, var(--panel-light) 100%);
    text-align: center;
  }
  .brand { position: absolute; left: 0; top: 60px; width: 372px; display: flex; flex-direction: column; align-items: center; gap: 14px; }
  .brand-square { width: 56px; height: 56px; background: var(--ink-soft); }
  .brand-name {
    font-family: "Cabin Condensed", sans-serif; font-weight: 500; color: var(--ink);
    font-size: 30px; line-height: 32px; letter-spacing: .5px;
  }
  .side-rule { position: absolute; left: 0; width: 372px; height: 2px; background: var(--rule); }
  .side-rule.top { top: 233px; }
  .side-rule.bottom { top: 453px; }
  .announcement {
    position: absolute; left: 0; top: 250px; width: 372px;
    font-size: 32px; line-height: 48px; color: var(--ink);
  }
  .announcement .accent { color: var(--green); }
  .contact { position: absolute; left: 0; width: 372px; display: flex; flex-direction: column; align-items: center; }
  .contact .icon {
    width: 44px; height: 44px; border-radius: 50%;
    background: radial-gradient(circle at 40% 35%, #ffffff 0%, #ececea 60%, #cfcfcc 100%);
    box-shadow: 0 1px 3px rgba(0,0,0,.25);
    display: flex; align-items: center; justify-content: center;
  }
  .contact .value {
    margin-top: 8px; font-family: "Abel", sans-serif; font-size: 20px; letter-spacing: 2px; color: var(--ink);
  }
  .contact.phone { top: 487px; }
  .contact.email { top: 580px; }
  .contact.web { top: 673px; }
  .field-rule { position: absolute; left: 372px; height: 1px; background: rgba(140,140,130,.45); }
  .tag {
    position: absolute; left: 395px; background: var(--tag); color: var(--ink);
    font-size: 26px; line-height: 30px; padding: 10px 14px;
  }
  .tag .accent { color: var(--green); }
  .tag.lead { top: 56px; width: 370px; font-size: 30px; line-height: 40px; padding: 4px 14px 8px; }
  .tag.reuse { top: 292px; width: 505px; }
  .tag.pay { top: 390px; width: 238px; }
  .tag.start { top: 488px; width: 415px; }
  .tag.close { top: 632px; width: 380px; font-size: 30px; line-height: 38px; padding: 8px 14px 10px; }
  .medallion {
    position: absolute; left: 930px; width: 230px; height: 230px; border-radius: 50%;
    background: radial-gradient(circle at 45% 35%, #ffffff 0%, #f4f4f2 55%, #dcdcd8 100%);
    box-shadow: 0 2px 8px rgba(0,0,0,.25);
    overflow: hidden; display: flex; align-items: center; justify-content: center;
  }
  .medallion.bin { top: 5px; }
  .medallion.exchange { top: 270px; flex-direction: column; gap: 4px; }
  .medallion.payout { top: 521px; }
  .photo { border-radius: 10px; }
  .photo.bin-shot { width: 100px; height: 190px; border-radius: 14px; background: linear-gradient(90deg, #1d6e2a, #3aa048 45%, #1f7a2e); }
  .photo.scrap-shot { width: 150px; height: 70px; background: linear-gradient(135deg, #b9b3a7, #8f9aa0 45%, #6b7f5c 70%, #c9c3b8); }
  .photo.cash-shot { width: 190px; height: 130px; background: linear-gradient(160deg, #c8cfbd, #9aa68c 50%, #b9c2aa); }
  .plus { font-size: 40px; line-height: 34px; color: var(--ink); }
  .mini-name { font-size: 15px; line-height: 16px; color: var(--ink); font-weight: 500; text-align: center; }
  .link-arrow { position: absolute; left: 1038px; width: 14px; height: 14px; }
  .link-arrow.first { top: 261px; }
  .link-arrow.second { top: 511px; }
</style>
</head>
<body>
<main class="postcard">
  <div class="backdrop" role="img" aria-label="Soft folded white paper texture background"></div>

  <aside class="side-panel">
    <div class="brand">
      <span class="brand-square"></span>
      <span class="brand-name">bramblecrest<br>resource group</span>
    </div>
    <div class="side-rule top"></div>
    <p class="announcement">
      <span class="accent">Now servicing</span><br>businesses<br>in the city of<br><span class="accent">Industry!</span>
    </p>
    <div class="side-rule bottom"></div>

    <div class="contact phone">
      <span class="icon"><svg width="22" height="22" viewBox="0 0 24 24"><path fill="#79bd43" d="M6.6 10.8a15.1 15.1 0 0 0 6.6 6.6l2.2-2.2c.3-.3.7-.4 1-.2 1.1.4 2.3.6 3.6.6.6 0 1 .4 1 1V20c0 .6-.4 1-1 1C10.6 21 3 13.4 3 4c0-.6.4-1 1-1h3.5c.6 0 1 .4 1 1 0 1.3.2 2.5.6 3.6.1.3 0 .7-.2 1z"/></svg></span>
      <span class="value">800.514.2976</span>
    </div>
    <div class="contact email">
      <span class="icon"><svg width="22" height="22" viewBox="0 0 24 24"><text x="12" y="18" text-anchor="middle" font-family="Arial, sans-serif" font-size="19" font-weight="bold" fill="#79bd43">@</text></svg></span>
      <span class="value">DELPHINE@BRAMBLE722.COM</span>
    </div>
    <div class="contact web">
      <span class="icon"><svg width="22" height="22" viewBox="0 0 24 24" fill="none" stroke="#79bd43" stroke-width="1.6"><circle cx="12" cy="12" r="9"/><ellipse cx="12" cy="12" rx="4" ry="9"/><path d="M3 12h18M5 7h14M5 17h14"/></svg></span>
      <span class="value">BRAMBLE722.COM</span>
    </div>
  </aside>

  <div class="field-rule" style="top:233px;width:500px"></div>
  <div class="field-rule" style="top:588px;width:560px"></div>

  <p class="tag lead">Companies choose<br>bramblecrest <span class="accent">Resource</span> Group<br>because:</p>
  <p class="tag reuse">if it can be recycled we will find a use for it</p>
  <p class="tag pay">we pay top dollar</p>
  <p class="tag start">starting our service is fast and easy</p>
  <p class="tag close">All it takes is one call/email<br>and we will handle the rest</p>

  <div class="medallion bin">
    <div class="photo bin-shot" role="img" aria-label="Green recycling bin"></div>
  </div>
  <svg class="link-arrow first" viewBox="0 0 14 14"><circle cx="7" cy="7" r="6" fill="#e4e4e0" stroke="#b0b0aa"/><path d="M4 6l3 3 3-3" fill="none" stroke="#777" stroke-width="1.3"/></svg>
  <div class="medallion exchange">
    <div class="photo scrap-shot" role="img" aria-label="Pile of mixed recyclable waste"></div>
    <span class="plus">+</span>
    <span class="mini-name">bramblecrest<br>resource group</span>
  </div>
  <svg class="link-arrow second" viewBox="0 0 14 14"><circle cx="7" cy="7" r="6" fill="#e4e4e0" stroke="#b0b0aa"/><path d="M4 6l3 3 3-3" fill="none" stroke="#777" stroke-width="1.3"/></svg>
  <div class="medallion payout">
    <div class="photo cash-shot" role="img" aria-label="Stacks of banknotes"></div>
  </div>
</main>
</body>
</html>
```